Weightloss company needs Business Card

We want a business card that is clean and professional, yet portrays that we are a friendly, innovative, and versatile program designed to fit the needs of our clients.
I would like there to be 2 sides, one side having an appointment card, and the other side containing the logo and business information. There can be decorations on both sides. The logo is attached.

Target Market(s)

Men and women 40-60

Industry/Entity Type

Business

Contact Information for Business Card

Font styles to use
Sans Serif

Requirements
Must have
• The logo, space for business information
Nice to have
• The colors in the logo
Should not have
• No pictures of people or food

```html
<!DOCTYPE html>
<html lang="en">
<head>
<meta charset="utf-8">
<title>Brightpath Weightloss – Business Card</title>
<link href="https://fonts.googleapis.com/css2?family=Open+Sans:wght@400;700&display=swap" rel="stylesheet">
<style>
  :root {
    --brand-red: #ec1c3c;
    --brand-cyan: #2ad4f6;
    --ink-grey: #4a4a4a;
    --ink-dark: #222;
    --card-white: #ffffff;
    --backdrop: #ecebe8;
  }
  * { box-sizing: border-box; margin: 0; padding: 0; }
  html, body { width: 1200px; height: 900px; overflow: hidden; }
  body {
    background: var(--backdrop);
    font-family: "Open Sans", sans-serif;
    position: relative;
  }
  .card {
    position: absolute;
    width: 630px;
    height: 360px;
    background: var(--card-white);
    box-shadow: 0 6px 18px rgba(0,0,0,.18);
    overflow: hidden;
  }

  .brand-name {
    font-weight: 700;
    color: var(--brand-red);
    letter-spacing: -0.5px;
    display: flex;
    align-items: center;
    gap: 10px;
    white-space: nowrap;
  }
  .brand-name .brand-dot {
    width: 14px; height: 14px; border-radius: 50%;
    background: var(--brand-cyan);
    flex: none;
  }

  /* Appointment side */
  .card--appointment { left: 500px; top: 70px; }
  .card--appointment .brand-name {
    position: absolute; left: 0; right: 0; top: 28px;
    justify-content: center; font-size: 30px;
  }
  .appointment-heading {
    position: absolute; left: 0; right: 0; top: 92px;
    text-align: center;
    color: var(--brand-red);
    font-weight: 700;
    font-size: 24px;
  }
  .appointment-field {
    position: absolute; left: 40px; right: 40px;
    display: flex; align-items: flex-end;
    font-size: 17px; font-weight: 700;
    color: var(--brand-red);
  }
  .appointment-field .field-line {
    flex: 1;
    border-bottom: 3px dotted var(--ink-dark);
    margin-left: 6px;
    height: 18px;
  }
  .appointment-field .field-unit { color: var(--ink-dark); margin: 0 4px; }
  .field-name { top: 148px; }
  .field-date { top: 186px; }
  .field-time { top: 224px; }
  .appointment-note {
    position: absolute; left: 40px; right: 40px; top: 292px;
    color: var(--brand-red); font-weight: 700; font-size: 17px;
  }

  /* Contact side */
  .card--contact { left: 80px; top: 470px; }
  .corner-accent { position: absolute; left: 0; top: 0; }
  .person { position: absolute; left: 70px; top: 26px; }
  .person-name { color: var(--brand-red); font-weight: 700; font-size: 20px; line-height: 1.1; }
  .person-title { color: var(--ink-grey); font-size: 16px; }
  .contact-list {
    position: absolute; left: 40px; top: 150px;
    list-style: none; color: var(--ink-grey); font-size: 16px; line-height: 1.35;
  }
  .contact-list li { display: flex; align-items: center; gap: 10px; }
  .contact-list .address { padding-left: 24px; }
  .contact-list svg { width: 14px; height: 14px; flex: none; }
  .card--contact .brand-name {
    position: absolute; right: 36px; top: 160px; font-size: 26px;
  }
  .bottom-bands { position: absolute; left: 0; bottom: 0; }
</style>
</head>
<body>

<section class="card card--appointment" aria-label="Appointment card">
  <div class="brand-name"><span>Brightpath Weightloss</span><span class="brand-dot"></span></div>
  <p class="appointment-heading">Your Next Appointment is</p>
  <div class="appointment-field field-name"><span>Name:</span><span class="field-line"></span></div>
  <div class="appointment-field field-date"><span>Date:</span><span class="field-line"></span></div>
  <div class="appointment-field field-time">
    <span>Time:</span><span class="field-line"></span><span class="field-unit">AM</span><span class="field-line"></span><span class="field-unit">PM</span>
  </div>
  <p class="appointment-note">If unable to keep appointment, kindly give 24hrs notice.</p>
</section>

<section class="card card--contact" aria-label="Business details card">
  <svg class="corner-accent" width="60" height="60" viewBox="0 0 60 60" aria-hidden="true">
    <rect x="0" y="0" width="36" height="30" fill="var(--brand-cyan)"/>
    <polygon points="28,0 56,0 50,56 14,56" fill="var(--brand-red)"/>
  </svg>
  <div class="person">
    <p class="person-name">Daniel Harper</p>
    <p class="person-title">Managing Director</p>
  </div>
  <ul class="contact-list">
    <li class="address">48 Sample Street Here</li>
    <li class="address">Region Name, 654321.</li>
    <li>
      <svg viewBox="0 0 16 16" aria-hidden="true"><path d="M4 1l3 3-2 2c1 2 3 4 5 5l2-2 3 3-2 3C7 15 1 9 1 3z" fill="var(--brand-red)"/></svg>
      044-555 010 200
    </li>
    <li>
      <svg viewBox="0 0 16 16" aria-hidden="true"><rect x="1" y="3" width="14" height="10" fill="var(--brand-red)"/><path d="M1 3l7 6 7-6" stroke="#fff" stroke-width="1.5" fill="none"/></svg>
      hello@brightpath.example
    </li>
    <li>
      <svg viewBox="0 0 16 16" aria-hidden="true"><circle cx="8" cy="8" r="7" fill="var(--brand-red)"/><path d="M1 8h14M8 1c3 3 3 11 0 14M8 1c-3 3-3 11 0 14" stroke="#fff" stroke-width="1" fill="none"/></svg>
      www.brightpath.example
    </li>
  </ul>
  <div class="brand-name"><span>Brightpath Weightloss</span><span class="brand-dot"></span></div>
  <svg class="bottom-bands" width="630" height="80" viewBox="0 0 630 80" aria-hidden="true">
    <polygon points="0,0 290,30 290,80 0,80" fill="var(--brand-cyan)"/>
    <polygon points="300,20 630,40 630,80 270,80" fill="var(--brand-red)"/>
  </svg>
</section>

</body>
</html>
```